Initial website for sport tech startup

We are currently in the R&D phases of our new product. It’s a headband to prevent concussion in the soccer market initially.

We have 2 products, one that’s basic aimed at the youth market and the other more technology driven that’s aimed at the academies and professional market.

Initially the product will launch in the UK

Target Market(s)

Youth soccer players and parents in UK, Soccer Clubs, Federations.

Industry/Entity Type

Sporting Good

Coding

Coded - Design and coding required

Number of Pages Required

5+ page

Requirements
Must have
• Professional style that can be adapted and changed over the coming months.
Nice to have
• Ecommerce ability in the future.

```html
<!DOCTYPE html>
<html lang="en">
<head>
<meta charset="utf-8">
<title>Headward – Head Protection for Football</title>
<link href="https://fonts.googleapis.com/css2?family=Lato:ital,wght@0,400;0,700;1,400&family=Raleway:wght@500;600;700;800&display=swap" rel="stylesheet">
<style>
:root{
  --navy:#2c4f8c;
  --navy-dark:#1f3f78;
  --ink:#222;
  --text:#6b6b6b;
  --muted:#9a9a9a;
  --grey-circle:#67625f;
  --grey-band:#eceeee;
  --dark:#2e2e2e;
  --darker:#4b4b4b;
  --white:#fff;
}
*{box-sizing:border-box;margin:0;padding:0}
html,body{width:1200px;height:3776px;overflow:hidden}
body{position:relative;background:var(--white);font-family:'Lato',sans-serif;color:var(--text)}
.abs{position:absolute}
a{color:inherit;text-decoration:none}

/* header */
.site-header{position:absolute;left:0;top:0;width:1200px;height:91px;background:var(--white)}
.brand{position:absolute;left:111px;top:21px;width:208px;height:49px;border:3px solid var(--navy);display:flex;align-items:center;justify-content:center;font-family:'Raleway',sans-serif;font-weight:700;font-size:34px;letter-spacing:1px;color:var(--navy)}
.main-nav{position:absolute;left:398px;top:37px;display:flex;gap:34px;font-size:14px;font-weight:700;color:var(--ink)}
.main-nav .active{color:var(--navy)}
.btn{display:inline-flex;align-items:center;gap:9px;background:var(--navy);color:var(--white);font-weight:700;font-size:14px;border-radius:2px}
.login{position:absolute;left:975px;top:24px;width:113px;height:44px;justify-content:center}

/* hero */
.hero{position:absolute;left:0;top:91px;width:1200px;height:557px;background:radial-gradient(ellipse at 75% 40%,#8a9a92 0%,#4e5f5e 40%,#2d3837 75%),#3a4545}
.hero::after{content:"";position:absolute;left:0;bottom:0;width:100%;height:160px;background:linear-gradient(180deg,rgba(70,90,40,0),#5a6e2f)}
.hero-frame{position:absolute;left:111px;top:111px;width:524px;height:297px;border:4px solid var(--white);z-index:1}
.hero-title{position:absolute;left:30px;top:30px;font-family:'Raleway',sans-serif;font-weight:800;font-size:62px;color:var(--white);letter-spacing:2px}
.hero-lead{position:absolute;left:33px;top:124px;width:460px;font-size:14px;line-height:22px;color:var(--white)}
.hero .btn{position:absolute;left:33px;top:198px;height:49px;padding:0 18px;font-size:14px}

/* section headings */
.heading{font-family:'Raleway',sans-serif;font-size:26px;font-weight:800;color:var(--ink);letter-spacing:.5px}
.heading span{font-weight:500;color:#555}
.bar{width:44px;height:3px;background:var(--navy)}
.center{left:0;width:1200px;text-align:center}

/* product */
.product-visual{left:73px;top:784px;width:488px;height:259px;background:radial-gradient(ellipse at 50% 55%,#5b6570 0%,#8a929b 45%,#f4f5f6 75%)}
.product-copy{left:671px;top:800px;width:417px;font-size:14px;line-height:26.5px;text-align:justify}
.product .btn{left:672px;top:1070px;width:145px;height:47px;justify-content:center}

/* background */
.bg-photo{left:0;top:1213px;width:1200px;height:558px;background:linear-gradient(135deg,#d8c77a 0%,#b7c15a 40%,#6f9a34 75%,#3f6c1e 100%);clip-path:polygon(640px 0,1200px 0,1200px 558px,640px 558px,790px 279px)}
.bg-circle{left:113px;top:1389px;width:204px;height:204px;border-radius:50%;background:var(--grey-circle);color:var(--white);text-align:center;padding:48px 18px 0}
.bg-circle h3{font-size:15px;font-weight:700;margin-bottom:10px}
.bg-circle p{font-size:12px;line-height:19px}
.step-text{font-size:12.5px;line-height:19.5px;color:#666}
.step-num{font-family:'Raleway',sans-serif;font-size:66px;font-weight:500;color:transparent;-webkit-text-stroke:1px #e6e6e6}
.step-line{height:0;border-top:2px dashed #ccc}
.step-dot{width:8px;height:8px;border-radius:50%;background:#666}
.step-icon{width:70px;height:70px;border-radius:50%;background:var(--white);border:3px solid var(--navy);box-shadow:0 0 0 4px rgba(255,255,255,.7)}

/* opportunity */
.opp-copy{left:140px;top:1918px;width:920px;text-align:center;font-size:14px;line-height:30px}
.stat{width:240px;text-align:center}
.stat svg{display:block;margin:0 auto 14px}
.stat p{font-size:13.5px;font-weight:700;color:var(--ink);line-height:20px}

/* research */
.research{left:0;top:2347px;width:1200px;height:495px;background:var(--grey-band)}
.pin{width:190px;text-align:center}
.pin p{font-size:14px;line-height:23px;color:#777;margin-top:22px}

/* team */
.card{width:292px;height:300px;background:var(--white);box-shadow:0 1px 6px rgba(0,0,0,.15);padding:3px;text-align:center}
.card .portrait{height:217px}
.card h4{font-size:14px;font-weight:700;color:var(--ink);margin-top:26px}
.card em{display:block;font-size:12.5px;color:var(--muted);margin-top:10px}

/* newsletter & footer */
.newsletter{left:0;top:3403px;width:1200px;height:311px;background:var(--dark)}
.news-title{font-family:'Raleway',sans-serif;font-size:26px;font-weight:800;color:var(--white)}
.news-form{left:334px;top:3532px;width:532px;height:47px;background:var(--white);border:2px solid var(--navy);display:flex;align-items:center}
.news-form .field{flex:1;display:flex;align-items:center;gap:12px;padding-left:22px;font-size:14px;color:#777}
.news-form .btn{height:43px;width:156px;justify-content:center;border-radius:0}
.foot-nav{left:0;top:3665px;width:1200px;display:flex;justify-content:center;gap:14px;font-size:14px;font-weight:700;color:var(--white)}
.foot-nav i{font-style:normal;font-weight:400}
.legal{left:0;top:3714px;width:1200px;height:62px;background:var(--darker);color:#e6e6e6;font-size:13.5px}
</style>
</head>
<body>

<header class="site-header">
  <div class="brand">HEADWARD</div>
  <nav class="main-nav">
    <a class="active">HOME</a><a>ABOUT US</a><a>PRODUCT</a><a>OUR TEAM</a><a>CONTACT US</a>
  </nav>
  <a class="btn login">LOG IN
    <svg width="11" height="12" viewBox="0 0 11 12"><rect x="1" y="5" width="9" height="7" fill="#fff"/><path d="M3 5V3.5a2.5 2.5 0 015 0V5" stroke="#fff" stroke-width="1.6" fill="none"/></svg>
  </a>
</header>

<section class="hero" role="img" aria-label="Close-up of a footballer's boot striking the pitch with turf flying, stadium lights behind">
  <div class="hero-frame">
    <h1 class="hero-title">HEADWARD</h1>
    <p class="hero-lead">Lorem ipsum dolor sit amet, consectetur adipiscing elit, sed do eiusmod tempor incididunt ut labore et dolore magna aliqua.</p>
    <a class="btn">GET STARTED
      <svg width="13" height="13" viewBox="0 0 13 13"><circle cx="6.5" cy="6.5" r="6.5" fill="#fff"/><path d="M5 3.5l3 3-3 3" stroke="#2c4f8c" stroke-width="1.8" fill="none"/></svg>
    </a>
  </div>
</section>

<section class="product">
  <div class="abs product-visual" role="img" aria-label="Illustration of the grey padded protective headband"></div>
  <h2 class="abs heading" style="left:671px;top:728px">OUR <span>PRODUCT</span></h2>
  <div class="abs bar" style="left:671px;top:772px"></div>
  <p class="abs product-copy">Sed ut perspiciatis unde omnis iste natus error sit voluptatem accusantium doloremque laudantium, totam rem aperiam, eaque ipsa quae ab illo inventore veritatis et quasi architecto beatae vitae dicta sunt explicabo. Nemo enim ipsam voluptatem quia voluptas sit aspernatur aut odit aut fugit, sed quia consequuntur magni dolores eos qui ratione voluptatem sequi nesciunt.<br>Sed ut perspiciatis unde omnis iste natus error sit voluptatem accusantium doloremque laudantium, totam rem aperiam, eaque ipsa quae ab illo inventore veritatis et quasi .</p>
  <a class="abs btn">READ MORE
    <svg width="13" height="13" viewBox="0 0 13 13"><circle cx="6.5" cy="6.5" r="6.5" fill="#fff"/><path d="M5 3.5l3 3-3 3" stroke="#2c4f8c" stroke-width="1.8" fill="none"/></svg>
  </a>
</section>

<section class="background">
  <div class="abs bg-photo" role="img" aria-label="Football resting on a sunlit grass pitch beside a player's boot"></div>
  <div class="abs bg-circle">
    <h3>BACKGROUND</h3>
    <p>More and more conversations are being had concussion as a result of sporting injuries; a debate.</p>
  </div>

  <!-- step 01 -->
  <p class="abs step-text" style="left:270px;top:1276px;width:200px">In the last 18 months, there has been an increased awareness.<br>&nbsp;of concussion symptoms.</p>
  <div class="abs step-num" style="left:500px;top:1258px">01</div>
  <div class="abs step-dot" style="left:480px;top:1297px"></div>
  <div class="abs step-line" style="left:488px;top:1300px;width:150px"></div>
  <!-- step 02 -->
  <p class="abs step-text" style="left:323px;top:1377px;width:215px">Football is the highest participation team.sport in the UK; it cuts across language, politics.</p>
  <div class="abs step-num" style="left:558px;top:1360px">02</div>
  <div class="abs step-dot" style="left:539px;top:1399px"></div>
  <div class="abs step-line" style="left:547px;top:1402px;width:135px"></div>
  <!-- step 03 -->
  <p class="abs step-text" style="left:360px;top:1477px;width:195px">Increased participation rates across England, Scotland, Wales and Northern</p>
  <div class="abs step-num" style="left:587px;top:1460px">03</div>
  <div class="abs step-dot" style="left:568px;top:1500px"></div>
  <div class="abs step-line" style="left:576px;top:1503px;width:150px"></div>
  <!-- step 04 -->
  <p class="abs step-text" style="left:325px;top:1574px;width:195px">Greater awareness and debate around neurodegenerative disease in former.</p>
  <div class="abs step-num" style="left:543px;top:1565px">04</div>
  <div class="abs step-dot" style="left:524px;top:1603px"></div>
  <div class="abs step-line" style="left:532px;top:1606px;width:150px"></div>
  <!-- step 05 -->
  <p class="abs step-text" style="left:262px;top:1686px;width:200px">Now is the opportunity to bring to market a incorporating temperature.</p>
  <div class="abs step-num" style="left:495px;top:1675px">05</div>
  <div class="abs step-dot" style="left:475px;top:1714px"></div>
  <div class="abs step-line" style="left:483px;top:1717px;width:150px"></div>

  <div class="abs step-icon" style="left:639px;top:1255px"><svg width="64" height="64" viewBox="0 0 64 64"><circle cx="32" cy="32" r="12" fill="none" stroke="#2c4f8c" stroke-width="2"/><circle cx="32" cy="32" r="3" fill="#2c4f8c"/></svg></div>
  <div class="abs step-icon" style="left:683px;top:1357px"><svg width="64" height="64" viewBox="0 0 64 64"><circle cx="34" cy="28" r="10" fill="none" stroke="#2c4f8c" stroke-width="2"/><path d="M20 46l8-8" stroke="#2c4f8c" stroke-width="2"/></svg></div>
  <div class="abs step-icon" style="left:727px;top:1459px"><svg width="64" height="64" viewBox="0 0 64 64"><circle cx="32" cy="32" r="12" fill="none" stroke="#2c4f8c" stroke-width="2"/><path d="M22 32h20M32 22v20" stroke="#2c4f8c" stroke-width="1.5"/></svg></div>
  <div class="abs step-icon" style="left:683px;top:1562px"><svg width="64" height="64" viewBox="0 0 64 64"><circle cx="32" cy="26" r="8" fill="none" stroke="#2c4f8c" stroke-width="2"/><path d="M18 46c4-8 24-8 28 0" stroke="#2c4f8c" stroke-width="2" fill="none"/></svg></div>
  <div class="abs step-icon" style="left:632px;top:1674px"><svg width="64" height="64" viewBox="0 0 64 64"><circle cx="38" cy="28" r="8" fill="none" stroke="#2c4f8c" stroke-width="2"/><path d="M20 22v20h10" stroke="#2c4f8c" stroke-width="2" fill="none"/></svg></div>
</section>

<section class="opportunity">
  <h2 class="abs heading center" style="top:1846px">SIZE OF THE &nbsp;<span>OPPORTUNITY</span></h2>
  <div class="abs bar" style="left:578px;top:1892px"></div>
  <p class="abs opp-copy">A day doesn't go by without a report of a game being held up for a concussion injury or a player being stretchered off up and down the country on a weekend, from youth football to men's and women's Sunday league. In youth and high school soccer athletes, a concussion is the second most common injury sustained during match play. More disturbing is that near half of players would not report the injury. Concussion is now a topic of national conversation level; in the media spotlight, on the radar of politicians and a top agenda item of sporting club, unions and federations.</p>

  <div class="abs stat" style="left:202px;top:2122px">
    <svg width="94" height="94" viewBox="0 0 94 94"><circle cx="47" cy="47" r="44" fill="none" stroke="#666" stroke-width="3"/><circle cx="47" cy="47" r="39" fill="none" stroke="#aaa" stroke-width="5" stroke-dasharray="1.5 2"/><text x="47" y="56" text-anchor="middle" font-family="Raleway,sans-serif" font-weight="700" font-size="27" fill="#2c4f8c">40%</text></svg>
    <p>INJURY FROM HEAD TO<br>PLAYER CONTAC</p>
  </div>
  <div class="abs stat" style="left:481px;top:2122px">
    <svg width="94" height="94" viewBox="0 0 94 94"><circle cx="47" cy="47" r="44" fill="none" stroke="#666" stroke-width="3"/><circle cx="47" cy="47" r="39" fill="none" stroke="#aaa" stroke-width="5" stroke-dasharray="1.5 2"/><text x="47" y="56" text-anchor="middle" font-family="Raleway,sans-serif" font-weight="700" font-size="27" fill="#2c4f8c">10%</text></svg>
    <p>INJURY FROM HEAD TO<br>GROUND</p>
  </div>
  <div class="abs stat" style="left:759px;top:2122px">
    <svg width="94" height="94" viewBox="0 0 94 94"><circle cx="47" cy="47" r="44" fill="none" stroke="#666" stroke-width="3"/><circle cx="47" cy="47" r="39" fill="none" stroke="#aaa" stroke-width="5" stroke-dasharray="1.5 2"/><text x="47" y="56" text-anchor="middle" font-family="Raleway,sans-serif" font-weight="700" font-size="27" fill="#2c4f8c">12%</text></svg>
    <p>INJURY FROM HEAD TO<br>BALL</p>
  </div>
</section>

<section class="abs research" role="img" aria-label="Faded background of a footballer and ball on a pale grey wash">
  <h2 class="abs heading center" style="top:49px">RESEARCH &nbsp;<span>CONCLUSIONS</span></h2>
  <div class="abs bar" style="left:578px;top:95px"></div>

  <div class="abs pin" style="left:112px;top:157px">
    <svg width="130" height="180" viewBox="0 0 130 180"><path d="M65 8a58 58 0 0141 99L65 136 24 107A58 58 0 0165 8z" fill="#fff" stroke="#2c4f8c" stroke-width="2"/><path d="M10 62A55 55 0 0140 14" stroke="#2c4f8c" stroke-width="5" fill="none"/><circle cx="65" cy="66" r="45" fill="#2c4f8c"/><text x="65" y="78" text-anchor="middle" font-family="Raleway,sans-serif" font-size="36" font-weight="600" fill="#fff">01</text><circle cx="65" cy="166" r="7" fill="none" stroke="#2c4f8c" stroke-width="2"/><circle cx="65" cy="166" r="3" fill="#2c4f8c"/></svg>
    <p>No specific head<br>protection product exists<br>for football.</p>
  </div>
  <div class="abs pin" style="left:308px;top:157px">
    <svg width="130" height="180" viewBox="0 0 130 180"><path d="M65 8a58 58 0 0141 99L65 136 24 107A58 58 0 0165 8z" fill="#fff" stroke="#67625f" stroke-width="2"/><path d="M10 62A55 55 0 0140 14" stroke="#67625f" stroke-width="5" fill="none"/><circle cx="65" cy="66" r="45" fill="#67625f"/><text x="65" y="78" text-anchor="middle" font-family="Raleway,sans-serif" font-size="36" font-weight="600" fill="#fff">02</text><circle cx="65" cy="166" r="7" fill="none" stroke="#67625f" stroke-width="2"/><circle cx="65" cy="166" r="3" fill="#67625f"/></svg>
    <p>Now represents the<br>opportunity to develop<br>a head protection.</p>
  </div>
  <div class="abs pin" style="left:504px;top:157px">
    <svg width="130" height="180" viewBox="0 0 130 180"><path d="M65 8a58 58 0 0141 99L65 136 24 107A58 58 0 0165 8z" fill="#fff" stroke="#2c4f8c" stroke-width="2"/><path d="M10 62A55 55 0 0140 14" stroke="#2c4f8c" stroke-width="5" fill="none"/><circle cx="65" cy="66" r="45" fill="#2c4f8c"/><text x="65" y="78" text-anchor="middle" font-family="Raleway,sans-serif" font-size="36" font-weight="600" fill="#fff">03</text><circle cx="65" cy="166" r="7" fill="none" stroke="#2c4f8c" stroke-width="2"/><circle cx="65" cy="166" r="3" fill="#2c4f8c"/></svg>
    <p>We have been in direct<br>contact and dialogue<br>with federations.</p>
  </div>
  <div class="abs pin" style="left:700px;top:157px">
    <svg width="130" height="180" viewBox="0 0 130 180"><path d="M65 8a58 58 0 0141 99L65 136 24 107A58 58 0 0165 8z" fill="#fff" stroke="#67625f" stroke-width="2"/><path d="M10 62A55 55 0 0140 14" stroke="#67625f" stroke-width="5" fill="none"/><circle cx="65" cy="66" r="45" fill="#67625f"/><text x="65" y="78" text-anchor="middle" font-family="Raleway,sans-serif" font-size="36" font-weight="600" fill="#fff">04</text><circle cx="65" cy="166" r="7" fill="none" stroke="#67625f" stroke-width="2"/><circle cx="65" cy="166" r="3" fill="#67625f"/></svg>
    <p>The nature of these<br>confidential discussions<br>has determined.</p>
  </div>
  <div class="abs pin" style="left:897px;top:157px">
    <svg width="130" height="180" viewBox="0 0 130 180"><path d="M65 8a58 58 0 0141 99L65 136 24 107A58 58 0 0165 8z" fill="#fff" stroke="#2c4f8c" stroke-width="2"/><path d="M10 62A55 55 0 0140 14" stroke="#2c4f8c" stroke-width="5" fill="none"/><circle cx="65" cy="66" r="45" fill="#2c4f8c"/><text x="65" y="78" text-anchor="middle" font-family="Raleway,sans-serif" font-size="36" font-weight="600" fill="#fff">05</text><circle cx="65" cy="166" r="7" fill="none" stroke="#2c4f8c" stroke-width="2"/><circle cx="65" cy="166" r="3" fill="#2c4f8c"/></svg>
    <p>Create and Develop<br>a product for the new<br>season starting.</p>
  </div>
</section>

<section class="team">
  <h2 class="abs heading center" style="top:2917px">MEET <span>OUR TEAM</span></h2>
  <div class="abs bar" style="left:578px;top:2962px"></div>

  <article class="abs card" style="left:126px;top:3005px">
    <div class="portrait" role="img" aria-label="Portrait photo of Martin Hale" style="background:linear-gradient(135deg,#c9262b,#d9b9a4 55%,#8a7a70)"></div>
    <h4>MARTIN HALE</h4><em>Founder / CEO</em>
  </article>
  <article class="abs card" style="left:451px;top:3005px">
    <div class="portrait" role="img" aria-label="Portrait photo of Fiona Kerr" style="background:linear-gradient(135deg,#cfd6de,#d9b3a0 55%,#2f3f6b)"></div>
    <h4>FIONA KERR</h4><em>Co - Founder / COO</em>
  </article>
  <article class="abs card" style="left:776px;top:3005px">
    <div class="portrait" role="img" aria-label="Portrait photo of Owen Larkin" style="background:linear-gradient(135deg,#e8e8e6,#c9a08a 55%,#7d8fb0)"></div>
    <h4>OWEN LARKIN</h4><em>CCO</em>
  </article>
</section>

<section class="abs newsletter">
  <h2 class="abs news-title center" style="top:58px">JOIN OUR NEWSLETTER</h2>
</section>
<form class="abs news-form">
  <div class="field">
    <svg width="15" height="11" viewBox="0 0 15 11"><rect x=".7" y=".7" width="13.6" height="9.6" fill="none" stroke="#777" stroke-width="1.2"/><path d="M1 1l6.5 5L14 1" stroke="#777" stroke-width="1.2" fill="none"/></svg>
    Enter Your Email
  </div>
  <a class="btn">SUBSCRIBE</a>
</form>
<nav class="abs foot-nav">
  <a>HOME</a><i>/</i><a>ABOUT US</a><i>/</i><a>OUR PRODUCTS</a><i>/</i><a>LATEST NEWS</a><i>/</i><a>BLOG</a><i>/</i><a>CONTACT US</a>
</nav>
<footer class="abs legal">
  <span class="abs" style="left:111px;top:22px">© 2020 Headward. All rights Reserved</span>
  <span class="abs" style="left:873px;top:22px">Terms Of Use &nbsp;/ &nbsp;Privacy Policy</span>
</footer>

</body>
</html>
```